Design a New Business Card for Our Company

We are looking for fresh, unique, and a modern business card that reflects our roots as digital marketing agency focused on SEM.

Industry/Entity Type

Marketing

Contact Information for Business Card

looking for very unique out of the box designs. clean and modern that compliments our logo

Requirements
Must have
• colors should match our logo
• Front should have name, address, email, and phone/fax of the person, phone/fax are the same number
• back should have our url

```html
<!DOCTYPE html>
<html lang="en">
<head>
<meta charset="utf-8">
<title>Clearpath Solutions — Business Card</title>
<link rel="stylesheet" href="https://fonts.googleapis.com/css2?family=Open+Sans:wght@400;600;700&display=swap">
<style>
  :root {
    --backdrop: #3a3430;
    --card: #0d0d0d;
    --card-edge: #1c1c1c;
    --brand-blue: #5b9bd5;
    --brand-grey: #bfbfbf;
    --text-light: #e6e6e6;
    --divider: #222222;
  }
  * { box-sizing: border-box; margin: 0; padding: 0; }
  html, body {
    width: 1200px; height: 900px; overflow: hidden;
    background: var(--backdrop);
    font-family: "Open Sans", Arial, sans-serif;
  }
  .canvas {
    position: relative; width: 1200px; height: 900px;
    display: flex; align-items: center; justify-content: center; gap: 60px;
  }
  .card {
    position: relative; width: 500px; height: 286px;
    background: var(--card);
    border: 1px solid var(--card-edge);
    box-shadow: 0 14px 30px rgba(0,0,0,.45);
    color: var(--text-light);
  }

  /* Front */
  .card-front { display: flex; }
  .front-mark {
    width: 230px; height: 100%;
    display: flex; align-items: center; justify-content: center; gap: 12px;
    border-right: 1px solid var(--divider);
  }
  .mark-dot { width: 26px; height: 26px; border-radius: 50%; background: var(--brand-blue); }
  .mark-name { font-size: 24px; font-weight: 700; color: var(--brand-grey); letter-spacing: -.5px; }
  .front-details { padding: 62px 0 0 34px; font-size: 14px; line-height: 1.3; white-space: nowrap; }
  .person-name { color: var(--brand-blue); font-weight: 600; font-size: 16px; }
  .person-role { font-size: 13px; margin-bottom: 22px; }
  .address { margin-bottom: 22px; }
  .contact-line { display: flex; align-items: center; gap: 8px; }
  .contact-line svg { width: 12px; height: 12px; fill: var(--brand-blue); flex: none; }

  /* Back */
  .card-back {
    display: flex; flex-direction: column; align-items: center; justify-content: center; gap: 26px;
  }
  .back-logo { display: flex; align-items: center; gap: 16px; }
  .back-logo .mark-dot { width: 40px; height: 40px; }
  .back-logo .mark-name { font-size: 40px; }
  .website { font-size: 13px; color: var(--text-light); }
</style>
</head>
<body>
<main class="canvas">
  <section class="card card-front" aria-label="Business card front">
    <div class="front-mark">
      <span class="mark-dot"></span>
      <span class="mark-name">clearpath</span>
    </div>
    <div class="front-details">
      <p class="person-name">Daniel Hartley</p>
      <p class="person-role">Managing Director</p>
      <p class="address">48 Harbour Lane, Suite 7<br>Westbridge, 204517.</p>
      <p class="contact-line">
        <svg viewBox="0 0 12 12" aria-hidden="true"><path d="M2 1h2.5l1 3-1.5 1a7 7 0 0 0 3 3l1-1.5 3 1V10a1 1 0 0 1-1 1A9 9 0 0 1 1 2a1 1 0 0 1 1-1z"/></svg>
        055-987 210 346
      </p>
      <p class="contact-line">
        <svg viewBox="0 0 12 12" aria-hidden="true"><path d="M1 2.5h10v7H1z M1.5 3l4.5 3.5L10.5 3" stroke="#0d0d0d" stroke-width="1"/></svg>
        daniel@clearpath.example
      </p>
    </div>
  </section>

  <section class="card card-back" aria-label="Business card back">
    <div class="back-logo">
      <span class="mark-dot"></span>
      <span class="mark-name">clearpath solutions</span>
    </div>
    <p class="website">www.clearpath.example</p>
  </section>
</main>
</body>
</html>
```